Emerging automotive detailing business

I am starting a small automotive detailing business in hopes of becoming a well-known detailer to work on high end cars. I would like a card to reflect the high quality and time I put into my work. The name of the company is Bright Crest Detailing. I feel like it represents racecars getting off the line at the drag strip as well as an innuendo of "Up the Ladder". I do minor paint correction such as clay barring, multi-step buffing and polishing, waxing, hand washes, etc. I am always striving to learn more and improve my work. My goal is to have total customer satisfaction. This is a female run business but I do not want it to be very girly. Elegant is okay! I have pictures of my personal wrenfield attached, they do not need to be incorporated but if you can think of a cool way to use 1 or all of them, go for it!

Target Market(s)

Anyone that owns a vehicle. Preferably high end vehicles such as Valtori, Castellverde and Morvani but I will also happily work on any car, truck or suv no matter what brand.

Industry/Entity Type

Automotive

Contact Information for Business Card

Bright Crest Detailing
Mira Tolland
4175 Quenhollow Rd
Ashmere PA 17492
Cell phone- call/text- 717-555-0148
email- brightcrestdetails@maildrop-example.com
Instagram: @brightcrestdetailing
Facebook: facebook.com/brightcrestdetailing

Requirements
Must have
• Business name, my name, address, phone number. Listing that I do minor paint correction such as clay barring, multi-step buffing and polishing, waxing, hand washes, interior cleaning, and more. (This last part was in nice to haves but I have realized that I do really want it, so I moved it to must haves.) I want something that is different and eye-catching to my customers. Some people have done this very well with cards already submitted to me, but a lot have not. I didn't mess with the "look and feel bars" much because because I am pretty open to the overall design as long as it is not your basic run of the mill design.
Nice to have
• Something car related. Maybe an appointment time/date line. I do not have a logo, but if you would like to design one and incorporate it, that would be amazing!
Should not have
• Purple and Pink colors. Boring, basic, normal card.

```html
<!DOCTYPE html>
<html lang="en">
<head>
<meta charset="utf-8">
<title>Bright Crest Detailing – Business Card</title>
<link href="https://fonts.googleapis.com/css2?family=Open+Sans:wght@400;600;700&display=swap" rel="stylesheet">
<style>
  :root {
    --backdrop: #3b3431;
    --card: #fbfbfb;
    --ink: #1e1e1e;
    --red: #e2232b;
    --faint: #eeeeee;
    --faint-ring: #ffffff;
  }
  * { box-sizing: border-box; margin: 0; padding: 0; }
  html, body { width: 1200px; height: 844px; overflow: hidden; }
  body {
    background: var(--backdrop);
    font-family: "Open Sans", Arial, sans-serif;
    color: var(--ink);
    display: flex;
    align-items: center;
    justify-content: center;
    gap: 50px;
  }
  .card {
    position: relative;
    width: 520px;
    height: 297px;
    background: var(--card);
    overflow: hidden;
    box-shadow: 0 10px 30px rgba(0,0,0,.45);
  }

  /* Brand lockup */
  .brand { position: absolute; display: flex; align-items: center; gap: 10px; }
  .brand-dot { width: 34px; height: 34px; border-radius: 50%; background: var(--red); flex: none; }
  .brand-name { font-weight: 400; line-height: 1; display: flex; flex-direction: column; align-items: flex-end; }
  .brand-name .primary { font-size: 34px; letter-spacing: 1px; }
  .brand-name .secondary { font-size: 21px; margin-top: 2px; }

  /* Front */
  .front .brand { top: 34px; right: 30px; color: var(--ink); }
  .front .faint-ring {
    position: absolute; right: -70px; top: 90px;
    width: 250px; height: 250px; border-radius: 50%;
    background: var(--faint);
    border: 12px solid var(--faint-ring);
    box-shadow: 0 0 0 6px var(--faint);
  }
  .contact { position: absolute; left: 30px; top: 150px; }
  .contact .person { color: var(--red); font-weight: 700; font-size: 17px; margin-bottom: 10px; }
  .contact .address { font-size: 13px; line-height: 1.55; margin-bottom: 12px; }
  .contact ul { list-style: none; font-size: 13px; line-height: 1.65; }
  .contact li { display: flex; align-items: center; gap: 9px; }
  .contact svg { width: 12px; height: 12px; flex: none; fill: var(--red); }
  .contact .square { width: 11px; height: 11px; background: var(--red); border-radius: 2px; flex: none; }

  /* Back */
  .appointment { position: absolute; top: 30px; left: 0; right: 0; padding: 0 40px; color: var(--red); }
  .appointment h2 {
    text-align: center; font-size: 15px; font-weight: 600;
    text-decoration: underline; text-underline-offset: 3px; margin-bottom: 22px;
  }
  .field { display: flex; align-items: flex-end; gap: 8px; font-size: 11px; font-weight: 600; margin-bottom: 16px; }
  .field .label { width: 40px; }
  .field .line { flex: 1; border-bottom: 1.5px dotted var(--ink); height: 12px; }
  .red-band { position: absolute; left: 0; right: 0; bottom: 0; height: 150px; background: var(--red); }
  .back .brand { bottom: 36px; right: 40px; color: #ffffff; }
  .back .brand-dot { background: #ffffff; }
</style>
</head>
<body>

<section class="card front" aria-label="Business card front">
  <div class="faint-ring"></div>
  <div class="brand">
    <span class="brand-dot"></span>
    <span class="brand-name"><span class="primary">BRIGHT CREST</span><span class="secondary">Detailing</span></span>
  </div>
  <div class="contact">
    <p class="person">Mira Tolland</p>
    <p class="address">4175 Quenhollow Rd<br>Ashmere PA 17492</p>
    <ul>
      <li><svg viewBox="0 0 24 24"><path d="M6.6 10.8a15.1 15.1 0 0 0 6.6 6.6l2.2-2.2a1 1 0 0 1 1-.25 11.4 11.4 0 0 0 3.6.57 1 1 0 0 1 1 1V20a1 1 0 0 1-1 1A17 17 0 0 1 3 4a1 1 0 0 1 1-1h3.5a1 1 0 0 1 1 1c0 1.25.2 2.45.57 3.57a1 1 0 0 1-.25 1z"/></svg>call/text- 717-555-0148</li>
      <li><svg viewBox="0 0 24 24"><path d="M2 5h20v14H2z M3 6l9 7 9-7" stroke="#fbfbfb" stroke-width="1.6"/></svg>brightcrestdetails@maildrop-example.com</li>
      <li><span class="square"></span>@brightcrestdetailing</li>
    </ul>
  </div>
</section>

<section class="card back" aria-label="Business card back">
  <div class="appointment">
    <h2>Your Next Appointment is</h2>
    <div class="field"><span class="label"></span><span class="line"></span></div>
    <div class="field"><span class="label">Date :</span><span class="line"></span><span>AM</span><span class="line"></span><span>PM</span></div>
    <div class="field"><span class="label">Time:</span><span class="line"></span></div>
  </div>
  <div class="red-band"></div>
  <div class="brand">
    <span class="brand-dot"></span>
    <span class="brand-name"><span class="primary">BRIGHT CREST</span><span class="secondary">Detailing</span></span>
  </div>
</section>

</body>
</html>
```